Real estate broker business card

Want a modern celan but effective business card for my residential and commercial real estate business. I want the back of the card to advertise my services and to capture business. I have attached the back of my current business card fore ideas
Updates

Logos, photo and text updates added! Added Saturday, September 3, 2016

Project Deadline Extended Reason: LOGOS, PHOTOS AND TEST JUST UPLOADED! I'M READY TO PICK A DESIGN! THANK YOU! Added Saturday, September 3, 2016

Target Market(s)

home buyers and seller. commercial buyers and sellers

Industry/Entity Type

Real Estate

Contact Information for Business Card

must have my contact information and my photo

Requirements
Must have
• Carla Ventrino
• Owner & Qualifying Broker
• Ventrino Real Estate Services
• 505.718.2094
• carla@ventrinohomes.example
• www.ventrinohomes.example
Nice to have
• metallic
• Business capture text: " Don't buy or lease property without someone looking out for your best interests. I will represent you on your home or investment purchase for FREE!"
• "Home owners, call today to receive a FREE market analysis for your homes value!

```html
<!DOCTYPE html>
<html lang="en">
<head>
<meta charset="utf-8">
<title>Ventrino Real Estate Services – Business Card</title>
<link href="https://fonts.googleapis.com/css2?family=Roboto:ital,wght@0,400;0,500;1,400&display=swap" rel="stylesheet">
<style>
  :root {
    --bg: #e9e6e1;
    --paper: #ffffff;
    --teal: #1a8c96;
    --teal-dark: #0b5f6b;
    --teal-deep: #08505b;
    --ink: #5b6166;
    --ink-soft: #7a8086;
    --white: #ffffff;
  }
  * { box-sizing: border-box; margin: 0; padding: 0; }
  html, body { width: 1200px; height: 950px; overflow: hidden; }
  body {
    background: var(--bg);
    font-family: "Roboto", Arial, sans-serif;
    position: relative;
  }
  .card {
    position: absolute;
    width: 700px;
    height: 400px;
    left: 250px;
    border-radius: 4px;
    box-shadow: 0 6px 18px rgba(0,0,0,.18);
    overflow: hidden;
  }
  .card--front { top: 50px; background: var(--paper); }
  .card--back {
    top: 500px;
    background: radial-gradient(ellipse at 40% 30%, var(--teal) 0%, var(--teal-dark) 70%, var(--teal-deep) 100%);
    color: var(--white);
  }

  /* front */
  .accent-strip {
    position: absolute; left: 46px; top: 0; width: 46px; height: 100%;
    background: linear-gradient(90deg, var(--teal-dark), var(--teal), var(--teal-dark));
  }
  .brand {
    position: absolute; display: flex; align-items: center; gap: 14px;
    font-weight: 500; letter-spacing: .06em; text-transform: uppercase;
  }
  .brand__dot { border-radius: 50%; flex: none; }
  .card--front .brand {
    left: 40px; top: 48px; color: var(--teal); font-size: 20px; line-height: 1.25;
  }
  .card--front .brand__name { max-width: 290px; }
  .card--front .brand__dot { width: 58px; height: 58px; background: var(--teal-dark); border: 4px solid var(--paper); }

  .photo {
    position: absolute; right: 34px; top: 30px; width: 230px; height: 140px;
    border-radius: 12px;
    background: linear-gradient(135deg, #2f4a2b 0%, #3c5a35 45%, #6f6a63 100%);
  }
  .contact {
    position: absolute; left: 130px; top: 190px; color: var(--ink);
  }
  .contact__name { color: var(--teal); font-size: 24px; font-weight: 500; margin-bottom: 6px; }
  .contact__line { font-size: 17px; line-height: 1.4; }
  .contact__list { list-style: none; margin-top: 12px; }
  .contact__list li {
    display: flex; align-items: center; gap: 10px;
    font-size: 16px; line-height: 1.7; color: var(--ink-soft);
  }
  .contact__list svg { width: 16px; height: 16px; fill: var(--ink); flex: none; }

  /* back */
  .card--back .brand {
    left: 110px; top: 120px; font-size: 34px; color: var(--white); line-height: 1.2;
  }
  .card--back .brand__name { max-width: 440px; }
  .card--back .brand__dot { width: 70px; height: 70px; background: var(--white); opacity: .9; }
  .pitch {
    position: absolute; left: 110px; top: 250px; width: 500px;
    font-size: 19px; font-style: italic; line-height: 1.45; color: var(--white);
  }
</style>
</head>
<body>

  <section class="card card--front">
    <div class="accent-strip"></div>
    <div class="brand">
      <span class="brand__dot"></span>
      <span class="brand__name">Ventrino Real Estate Services</span>
    </div>

    <div class="photo" role="img" aria-label="Portrait photo of Carla Ventrino"></div>

    <div class="contact">
      <p class="contact__name">Carla Ventrino</p>
      <p class="contact__line">Owner &amp; Qualifying Broker</p>
      <p class="contact__line">Ventrino Real Estate Services</p>
      <ul class="contact__list">
        <li>
          <svg viewBox="0 0 16 16" aria-hidden="true"><path d="M3.5 1l2.5 3-1.5 2c1 2 2.5 3.5 4.5 4.5l2-1.5 3 2.5-1.5 2.5C7 15 1 9 1 2.5z"/></svg>
          505.718.2094
        </li>
        <li>
          <svg viewBox="0 0 16 16" aria-hidden="true"><path d="M1 3h14v10H1z M1 3l7 6 7-6" fill="none" stroke="#5b6166" stroke-width="1.6"/></svg>
          carla@ventrinohomes.example
        </li>
        <li>
          <svg viewBox="0 0 16 16" aria-hidden="true"><circle cx="8" cy="8" r="7"/></svg>
          www.ventrinohomes.example
        </li>
      </ul>
    </div>
  </section>

  <section class="card card--back">
    <div class="brand">
      <span class="brand__dot"></span>
      <span class="brand__name">Ventrino Real Estate Services</span>
    </div>
    <p class="pitch">Don't buy or lease property without someone looking out for your best interests. I will represent you on your home or investment purchase for FREE!</p>
  </section>

</body>
</html>
```